CREATE A BUSINESS CARD FOR A BOAT CLEANING SERVICE

WE ARE STARTING A NEW BOAT CLEANING BUSINESS. WE DIVE UNDERWATER TO CLEAN BOAT HULLS, JETTIES, UNDERWATER STRUCTURES ETC. WE ARE LOOKING FOR AN UPPERMARKET MODERN LOGO AND BUSINESS CARD AS ALOT OF OUR TARGET MARKET WILL BE HIGH END. YOU HAVE TO DESIGN A BUSINESS CARD AND LOGO SEPERATELY .
THE BUSINESS CARD DIMESNION MUST BE STANDARD SIZE.
The standard dimensions of a printed business card are 3.5 x 2 inches

Target Market(s)

UNDERWATER SERVICED

Industry/Entity Type

Business

Contact Information for Business Card

HOLLAND UNDERWATER SERVICES

Font styles to use
Serif

Colors

Designer to choose colors to be used in the design.

Requirements
Must have
• HOLLAND
Nice to have
• dark
Should not have
• more than 3 colors

```html
<!DOCTYPE html>
<html lang="en">
<head>
<meta charset="utf-8">
<title>Holland Underwater Service – Business Card</title>
<link rel="stylesheet" href="https://fonts.googleapis.com/css2?family=Josefin+Sans:wght@400;600&family=Roboto:wght@300;400;500&display=swap">
<style>
  :root {
    --bg: #3b3631;
    --card-grey: #868787;
    --card-white: #ffffff;
    --brand-blue: #0f548c;
    --stripe-grey: #9a9b9c;
    --text-grey: #8a8a8a;
    --white: #ffffff;
    --ink: #1b1b1b;
  }
  * { margin: 0; padding: 0; box-sizing: border-box; }
  html, body {
    width: 1200px; height: 930px; overflow: hidden;
    background: var(--bg);
  }
  .stage { position: relative; width: 1200px; height: 930px; }

  .card {
    position: absolute; width: 540px; height: 309px;
    border-radius: 18px; overflow: hidden;
    box-shadow: 0 6px 18px rgba(0,0,0,.45);
  }

  /* back side */
  .card-back { left: 40px; top: 170px; background: var(--card-grey); }
  .card-back .logo { position: absolute; left: 0; right: 0; top: 108px; text-align: center; color: var(--white); }

  .logo-name {
    font-family: "Josefin Sans", sans-serif; font-weight: 600;
    font-size: 34px; letter-spacing: 18px; padding-left: 18px;
  }
  .logo-sub {
    font-family: "Josefin Sans", sans-serif; font-weight: 400;
    font-size: 15px; letter-spacing: 5px; margin-top: 6px;
  }

  /* front side */
  .card-front { left: 620px; top: 440px; background: var(--card-white); }
  .card-front svg.waves { position: absolute; inset: 0; }

  .person { position: absolute; right: 30px; top: 24px; text-align: right; color: var(--white); font-family: "Roboto", sans-serif; }
  .person-name { font-size: 25px; font-weight: 500; letter-spacing: .5px; }
  .person-role { font-size: 13px; font-weight: 300; margin-top: 1px; }

  .card-front .logo { position: absolute; left: 32px; top: 160px; color: var(--brand-blue); }
  .card-front .logo-name { font-size: 28px; letter-spacing: 14px; padding-left: 0; }
  .card-front .logo-sub { font-size: 12px; letter-spacing: 4px; color: var(--text-grey); }

  .partners { position: absolute; right: 34px; top: 136px; display: flex; align-items: center; gap: 18px; }
  .partner-badge { width: 42px; height: 42px; border-radius: 50%; background: var(--brand-blue); border: 3px solid #c9d6e2; }
  .alt-mark { display: flex; align-items: center; gap: 6px; font-family: "Josefin Sans", sans-serif; font-weight: 600; font-size: 20px; color: var(--ink); letter-spacing: 1px; }
  .alt-mark .dot { width: 26px; height: 26px; border-radius: 50%; background: var(--ink); }

  .rule { position: absolute; height: 1.5px; background: var(--brand-blue); }
  .rule-right { right: 34px; top: 188px; width: 250px; }
  .rule-left { left: 32px; top: 236px; width: 230px; }

  .contacts { position: absolute; right: 34px; top: 196px; list-style: none; font-family: "Roboto", sans-serif; font-size: 13px; color: var(--text-grey); text-align: right; line-height: 17px; }
  .contacts li { display: flex; justify-content: flex-end; align-items: center; gap: 8px; }
  .contacts svg { width: 10px; height: 10px; fill: var(--brand-blue); }

  .address { position: absolute; left: 32px; top: 248px; font-family: "Roboto", sans-serif; font-size: 13px; color: var(--text-grey); line-height: 17px; font-style: normal; }
</style>
</head>
<body>
<main class="stage">

  <section class="card card-back" aria-label="Card back">
    <div class="logo">
      <div class="logo-name">HOLLAND</div>
      <div class="logo-sub">UNDERWATER SERVICE</div>
    </div>
  </section>

  <section class="card card-front" aria-label="Card front">
    <svg class="waves" viewBox="0 0 540 309" preserveAspectRatio="none" aria-hidden="true">
      <path fill="#0f548c" d="M0,0 H540 V78 C470,116 380,118 290,102 C200,86 90,82 0,106 Z"/>
      <path fill="#9a9b9c" d="M0,106 C90,82 200,86 290,102 C380,118 470,116 540,78 V88 C470,128 380,130 290,114 C190,98 90,96 0,122 Z"/>
      <path fill="#0f548c" d="M0,128 C70,104 160,104 230,112 C150,112 80,120 34,150 C24,140 12,134 0,132 Z"/>
    </svg>

    <div class="person">
      <div class="person-name">MARTIN KELLER</div>
      <div class="person-role">President</div>
    </div>

    <div class="logo">
      <div class="logo-name">HOLLAND</div>
      <div class="logo-sub">UNDERWATER SERVICE</div>
    </div>

    <div class="partners">
      <div class="partner-badge" role="img" aria-label="Partner badge"></div>
      <div class="alt-mark"><span class="dot"></span>HOLLAND</div>
    </div>

    <div class="rule rule-right"></div>
    <ul class="contacts">
      <li>(410) 555-0182
        <svg viewBox="0 0 10 10"><path d="M2,0 L4,2.5 L3,3.8 C3.8,5.3 4.7,6.2 6.2,7 L7.5,6 L10,8 L8.5,10 C4,9.5 0.5,6 0,1.5 Z"/></svg></li>
      <li>info@hollandunderwater.com
        <svg viewBox="0 0 10 10"><path d="M0,2 H10 V8.5 H0 Z M0.8,2.6 L5,5.6 L9.2,2.6 V3.4 L5,6.4 L0.8,3.4 Z" fill-rule="evenodd"/></svg></li>
      <li>www.hollandunderwater.com
        <svg viewBox="0 0 10 10"><circle cx="5" cy="5" r="4.5"/><path d="M0.5,5 H9.5 M5,0.5 V9.5" stroke="#fff" stroke-width=".8"/></svg></li>
    </ul>

    <div class="rule rule-left"></div>
    <address class="address">
      300, 418 - 9th Ave, SW<br>Calgary, AB T2P 1K5
    </address>
  </section>

</main>
</body>
</html>
```